New Innovative Counselling and psychotherapy Service needs Business Card design

Keep it simple and professional. On one side, just company name and logo (perhaps in all blue) and maybe a tag line.

On other side (all white) my name and Qualifications in centre

Industry/Entity Type

Health And Wellness

Contact Information for Business Card

Dara Whelby
Counsellor & Psychotherapist
BSc (Psychol.), BA, Dip. (Couns. & Psych.), PG.Cert (CBT), FGTrK, ONRE

I will also require Mobile no, Email and web site address of which I'll pass on to final designer.

Font styles to use
Sans Serif

Requirements
Must have
• My Logo Only and please use the colours in logo that is in it.
Should not have
• Any other images

```html
<!DOCTYPE html>
<html lang="en">
<head>
<meta charset="utf-8">
<title>Hollin Grove – Business Card</title>
<link href="https://fonts.googleapis.com/css2?family=Arimo:wght@400;700&display=swap" rel="stylesheet">
<style>
  :root {
    --backdrop: #b9b9b9;
    --card-white: #f4f4f4;
    --card-dark: #333333;
    --brand-blue: #45b4ee;
    --brand-green: #98d45a;
    --ink: #333333;
    --white: #ffffff;
  }
  html, body {
    margin: 0;
    padding: 0;
    width: 1200px;
    height: 960px;
    overflow: hidden;
    background: var(--backdrop);
    font-family: "Arimo", Arial, sans-serif;
  }
  .canvas {
    position: relative;
    width: 1200px;
    height: 960px;
  }
  .card {
    position: absolute;
    width: 598px;
    height: 342px;
    border-radius: 18px;
    overflow: hidden;
  }
  /* Front */
  .card-front {
    left: 322px;
    top: 110px;
    background: var(--card-white);
  }
  .wordmark {
    position: absolute;
    left: 112px;
    top: 74px;
    display: flex;
    align-items: center;
    gap: 24px;
  }
  .wordmark-dot {
    width: 72px;
    height: 72px;
    border-radius: 50%;
    background: var(--brand-blue);
  }
  .wordmark-name {
    font-size: 38px;
    font-weight: 400;
    color: var(--ink);
    letter-spacing: -0.5px;
  }
  .band {
    position: absolute;
    top: 230px;
    height: 112px;
  }
  .band-identity {
    left: 0;
    width: 328px;
    background: var(--brand-blue);
    color: var(--white);
    padding: 16px 0 0 27px;
    box-sizing: border-box;
  }
  .band-contact {
    left: 330px;
    width: 268px;
    background: var(--brand-green);
    color: var(--white);
    padding: 29px 24px 0 0;
    box-sizing: border-box;
  }
  .person-name {
    margin: 0;
    font-size: 24px;
    font-weight: 700;
    line-height: 1;
  }
  .person-role {
    margin: 10px 0 0;
    font-size: 16px;
    font-weight: 700;
  }
  .person-quals {
    margin: 3px 0 0;
    font-size: 12.5px;
    font-weight: 700;
    line-height: 1.2;
  }
  .contact-list {
    list-style: none;
    margin: 0;
    padding: 0;
    text-align: right;
    font-size: 14px;
    line-height: 20px;
  }
  .contact-list li {
    display: flex;
    justify-content: flex-end;
    align-items: center;
    gap: 8px;
  }
  .contact-icon {
    width: 13px;
    height: 13px;
    flex: none;
  }
  /* Back */
  .card-back {
    left: 320px;
    top: 494px;
    background: var(--card-dark);
  }
  .back-mark {
    position: absolute;
    left: 0;
    right: 0;
    top: 62px;
    display: flex;
    flex-direction: column;
    align-items: center;
    gap: 22px;
  }
  .back-dot {
    width: 120px;
    height: 120px;
    border-radius: 50%;
    background: var(--brand-blue);
  }
  .back-name {
    font-size: 32px;
    font-weight: 400;
    color: var(--brand-blue);
  }
  .tagline {
    position: absolute;
    left: 0;
    right: 0;
    top: 288px;
    margin: 0;
    text-align: center;
    font-size: 14px;
    color: var(--white);
  }
</style>
</head>
<body>
<main class="canvas">
  <section class="card card-front" aria-label="Card front">
    <div class="wordmark">
      <span class="wordmark-dot"></span>
      <span class="wordmark-name">Hollin Grove</span>
    </div>
    <div class="band band-identity">
      <h1 class="person-name">Dara Whelby</h1>
      <p class="person-role">Counsellor &amp; Psychotherapist</p>
      <p class="person-quals">BSc (Psychol.), BA, Dip. (Couns. &amp; Psych.)<br>PG.Cert (CBT), FGTrK,</p>
    </div>
    <div class="band band-contact">
      <ul class="contact-list">
        <li>555 210 4718
          <svg class="contact-icon" viewBox="0 0 13 13"><rect x="3" y="0.5" width="7" height="12" rx="1.3" fill="none" stroke="#fff" stroke-width="1.4"/><rect x="5.5" y="10" width="2" height="1" fill="#fff"/></svg>
        </li>
        <li>dara@Hollingrove.com
          <svg class="contact-icon" viewBox="0 0 13 13"><rect x="0.5" y="2.5" width="12" height="8" fill="#fff"/><path d="M0.5 2.5 L6.5 7 L12.5 2.5" fill="none" stroke="#98d45a" stroke-width="1"/></svg>
        </li>
        <li>www.Hollingrove.com
          <svg class="contact-icon" viewBox="0 0 13 13"><circle cx="6.5" cy="6.5" r="6" fill="#fff"/><path d="M3 4 Q5 3 6 5 Q5 7 3.5 7 Z M8 8 Q10 7 10.5 9 Q9 11 8 10 Z" fill="#98d45a"/></svg>
        </li>
      </ul>
    </div>
  </section>

  <section class="card card-back" aria-label="Card back">
    <div class="back-mark">
      <span class="back-dot"></span>
      <span class="back-name">Hollin Grove</span>
    </div>
    <p class="tagline">Caring For Your Psychological Well-Being Is Our Top Priority</p>
  </section>
</main>
</body>
</html>
```